Coastline Premier Retreats Business Card Design

Design a business card for Coastline Premier Retreats. Look at the website for colors and reference. Card should have logo, name, title, office number, mobile number, email, URL and a tagline like, "Luxury Hotel & Resort Email Marketing" (This might change).

https://www.coastlinepremierretreats.example

The rest I will leave up to your imagination.

Contact Information for Business Card

Logo, name, title, office number, mobile number, email, URL and a tagline like, "Luxury Hotel & Resort Email Marketing" (This might change).

```html
<!DOCTYPE html>
<html lang="en">
<head>
<meta charset="utf-8">
<title>Coastline Premier Retreats – Business Card</title>
<link rel="stylesheet" href="https://fonts.googleapis.com/css2?family=Roboto:ital,wght@0,400;0,700;1,400&display=swap">
<style>
  :root {
    --stage: #7a7a7a;
    --card-dark: #000000;
    --card-light: #f4f4f4;
    --accent: #f07a12;
    --ink: #111111;
    --ink-soft: #5a5a5a;
    --paper-text: #ffffff;
  }
  * { box-sizing: border-box; margin: 0; padding: 0; }
  html, body {
    width: 1200px; height: 900px; overflow: hidden;
    background: var(--stage);
    font-family: "Roboto", Arial, sans-serif;
  }
  .stage {
    width: 1200px; height: 900px;
    display: flex; flex-direction: column;
    align-items: center; justify-content: center; gap: 60px;
  }
  .card {
    width: 560px; height: 320px;
    border-radius: 22px;
    position: relative;
    overflow: hidden;
  }

  /* Front */
  .card--front {
    background: var(--card-dark);
    border-bottom: 4px solid var(--accent);
    display: flex; flex-direction: column;
    align-items: center; justify-content: center;
  }
  .brand {
    display: flex; align-items: center; gap: 14px;
    margin-top: 10px;
  }
  .brand__square {
    width: 18px; height: 18px; background: var(--accent); flex: none;
  }
  .brand__name {
    color: var(--paper-text);
    font-weight: 700; font-size: 30px;
    letter-spacing: 2px; text-transform: uppercase; line-height: 1.1;
  }
  .front-url {
    position: absolute; bottom: 44px; left: 0; right: 0;
    text-align: center;
    font-size: 13px; letter-spacing: 2.5px;
    color: var(--paper-text);
  }
  .front-url__domain { color: var(--accent); }

  /* Back */
  .card--back {
    background: var(--card-light);
    padding: 30px 40px;
    color: var(--ink);
  }
  .back-brand {
    display: flex; align-items: center; gap: 10px;
    margin-bottom: 22px;
  }
  .back-brand__square { width: 12px; height: 12px; background: var(--accent); flex: none; }
  .back-brand__name {
    font-weight: 700; font-size: 17px; letter-spacing: 1.5px;
    text-transform: uppercase; color: var(--ink);
  }
  .person__name { font-weight: 700; font-size: 22px; letter-spacing: 0.5px; }
  .person__title { font-size: 14px; color: var(--ink-soft); margin-top: 2px; }
  .divider { width: 36px; height: 1px; background: var(--ink); margin: 16px 0 14px; }
  .contacts { list-style: none; font-size: 13.5px; line-height: 1.45; }
  .contacts__item { display: flex; align-items: center; gap: 10px; }
  .contacts__icon { width: 12px; height: 12px; flex: none; }
  .tagline { margin-top: 8px; font-size: 13.5px; }
</style>
</head>
<body>
<main class="stage">

  <section class="card card--front" aria-label="Card front">
    <div class="brand">
      <span class="brand__square"></span>
      <span class="brand__name">Coastline Premier Retreats</span>
    </div>
    <p class="front-url">www.<span class="front-url__domain">coastlinepremierretreats</span>.example</p>
  </section>

  <section class="card card--back" aria-label="Card back">
    <div class="back-brand">
      <span class="back-brand__square"></span>
      <span class="back-brand__name">Coastline Premier Retreats</span>
    </div>
    <h1 class="person__name">Daniel Reyes</h1>
    <p class="person__title">President</p>
    <div class="divider"></div>
    <ul class="contacts">
      <li class="contacts__item">
        <svg class="contacts__icon" viewBox="0 0 12 12"><path d="M2.5 1 L4.5 1 L5.3 3.3 L4 4.3 Q5 6.8 7.7 8 L8.7 6.7 L11 7.5 L11 9.5 Q10.5 11 9 11 Q1 9.5 1 2.5 Q1 1 2.5 1Z" fill="var(--accent)"/></svg>
        555.014.2000
      </li>
      <li class="contacts__item">
        <svg class="contacts__icon" viewBox="0 0 12 12"><rect x="3" y="0.8" width="6" height="10.4" rx="1" fill="none" stroke="var(--accent)" stroke-width="1.4"/><circle cx="6" cy="9.3" r="0.7" fill="var(--accent)"/></svg>
        555.014.2001
      </li>
      <li class="contacts__item">
        <svg class="contacts__icon" viewBox="0 0 12 12"><rect x="0.8" y="2.3" width="10.4" height="7.4" fill="none" stroke="var(--accent)" stroke-width="1.3"/><path d="M0.8 2.3 L6 6.5 L11.2 2.3" fill="none" stroke="var(--accent)" stroke-width="1.3"/></svg>
        info@coastlinepremierretreats.example
      </li>
      <li class="contacts__item">
        <svg class="contacts__icon" viewBox="0 0 12 12"><circle cx="6" cy="6" r="5" fill="none" stroke="var(--accent)" stroke-width="1.3"/><ellipse cx="6" cy="6" rx="2.2" ry="5" fill="none" stroke="var(--accent)" stroke-width="1"/><path d="M1 6 H11" stroke="var(--accent)" stroke-width="1"/></svg>
        www.coastlinepremierretreats.example
      </li>
    </ul>
    <p class="tagline">Luxury Hotel &amp; Resort Email Marketing</p>
  </section>

</main>
</body>
</html>
```